Tolvik Commercial Cleaning is lookong for a new business card design.

A fresh new design that's professional and stylish. We need a serious upgrade to our business cards. I have included pictures of our existing ones. Our clients include professional individuals and business owners. We woupdblike something professional and upbeat. Please have fun and see what you come uo with.

Target Market(s)

Property managers, business owners, facility managers and other similar professionals

Industry/Entity Type

Janitorial

Contact Information for Business Card

Name, cell, office number, email, web address

Font styles to use
Sans Serif

Colors

Designer to choose colors to be used in the design.

Requirements
Must have
• please use the green color in our logo
Nice to have
• Bar code
Should not have
• Address

```html
<!DOCTYPE html>
<html lang="en">
<head>
<meta charset="utf-8">
<title>Tolvik Commercial Cleaning – Business Card</title>
<link href="https://fonts.googleapis.com/css2?family=Open+Sans:wght@400;600;700&display=swap" rel="stylesheet">
<style>
  :root {
    --page-bg: #ecebe8;
    --card-blue: #3d72a9;
    --brand-green: #39b54a;
    --deep-green: #2a8f3a;
    --decor-teal: #3a8d99;
    --ink-white: #ffffff;
    --shadow: rgba(0, 0, 0, 0.18);
  }
  * { box-sizing: border-box; margin: 0; padding: 0; }
  html, body {
    width: 1200px; height: 780px; overflow: hidden;
    background: var(--page-bg);
    font-family: "Open Sans", Arial, sans-serif;
  }
  .canvas {
    position: relative; width: 1200px; height: 780px;
    display: flex; align-items: center; justify-content: center; gap: 50px;
  }
  .card {
    position: relative; width: 540px; height: 310px;
    border-radius: 22px; overflow: hidden;
    box-shadow: 0 10px 24px var(--shadow);
  }

  /* Front */
  .card-front { background: var(--card-blue); color: var(--ink-white); }
  .brand-name {
    position: absolute; left: 34px; top: 26px;
    color: var(--brand-green); font-weight: 700; line-height: 1.05;
  }
  .brand-name .word-main { display: block; font-size: 46px; letter-spacing: -0.5px; }
  .brand-name .word-sub { display: block; font-size: 16px; letter-spacing: 0.3px; margin-top: 4px; }
  .contact-list {
    position: absolute; left: 34px; top: 172px; list-style: none;
    font-size: 14px; line-height: 1.6;
  }
  .contact-list li { display: flex; align-items: center; gap: 8px; }
  .contact-list svg { width: 12px; height: 12px; flex: none; }
  .decor-name {
    position: absolute; right: 40px; top: 136px;
    color: var(--decor-teal); font-weight: 700; font-size: 96px;
    letter-spacing: -2px; line-height: 1;
  }
  .person {
    position: absolute; right: 64px; top: 166px; text-align: right;
  }
  .person-name { font-weight: 700; font-size: 26px; line-height: 1.1; }
  .person-title { font-weight: 400; font-size: 17px; margin-top: 2px; }
  .accent-band {
    position: absolute; right: 0; bottom: 34px;
    width: 44px; height: 64px; background: var(--brand-green);
  }

  /* Back */
  .card-back {
    background: var(--brand-green);
    display: flex; align-items: center; justify-content: center;
  }
  .back-name {
    color: var(--deep-green); font-weight: 700; text-align: center; line-height: 1.05;
  }
  .back-name .word-main { display: block; font-size: 84px; letter-spacing: -1.5px; }
  .back-name .word-sub { display: block; font-size: 24px; letter-spacing: 0.4px; margin-top: 6px; }
</style>
</head>
<body>
<main class="canvas">
  <section class="card card-front" aria-label="Business card front">
    <div class="brand-name">
      <span class="word-main">Tolvik</span>
      <span class="word-sub">Commercial Cleaning</span>
    </div>

    <ul class="contact-list">
      <li>
        <svg viewBox="0 0 12 12" aria-hidden="true"><path fill="#39b54a" d="M2.4 1l2 2.2-1 1.3a6.5 6.5 0 0 0 4.1 4.1l1.3-1 2.2 2-1.1 1.4C5.4 11 1 6.6.9 2.1z"/></svg>
        (555) 014-2287
      </li>
      <li>
        <svg viewBox="0 0 12 12" aria-hidden="true"><rect x="0.5" y="2" width="11" height="8" rx="1" fill="#39b54a"/><path d="M1 2.6l5 3.8 5-3.8" fill="none" stroke="#3d72a9" stroke-width="1"/></svg>
        maren@tolvikcleaning.com
      </li>
      <li>
        <svg viewBox="0 0 12 12" aria-hidden="true"><circle cx="6" cy="6" r="5.3" fill="#39b54a"/><path d="M.8 6h10.4M6 .7c-2.6 3-2.6 7.6 0 10.6M6 .7c2.6 3 2.6 7.6 0 10.6" fill="none" stroke="#3d72a9" stroke-width="0.8"/></svg>
        www.tolvikcleaning.com
      </li>
    </ul>

    <div class="decor-name" aria-hidden="true">Tolvik</div>

    <div class="person">
      <p class="person-name">Maren Ostby</p>
      <p class="person-title">Director</p>
    </div>

    <div class="accent-band" aria-hidden="true"></div>
  </section>

  <section class="card card-back" aria-label="Business card back">
    <div class="back-name">
      <span class="word-main">Tolvik</span>
      <span class="word-sub">Commercial Cleaning</span>
    </div>
  </section>
</main>
</body>
</html>
```